Vernac Law Business cards and stationary design project

We are looking for a stationary design for business cards (double sided), 8x10, 5x7, and legal and standard envelopes.

We would like the design to match the logo that we have already.
Color palate preferred is Teal, White, grey and any others that will look good for a professional law firm.

We would like this statement: "INTEGRITY. COUNSEL. RESOLVE" to be on the back of the business cards and maybe on the stationary if it looks good.

Please see link to website for more information: www.vernac-law.example

Target Market(s)

Potential clients that need Attorney services.

Industry/Entity Type

Law Firm

Contact Information for Business Card

We would like the front and back to be two different colors. Current business cards are teal front, grey back and are a vertical design. We are open to options with colors.

Font styles to use
Serif

Colors
33a6d7
33b8a4
b9b9b9
5c5c5c

Requirements
Must have
• Logo supplied needs to go on the card and stationary.
• Match website color palate, www.vernac-law.example
• Be professional and not too wordy.
• Criminal Law, Civil Litigation, Personal Injury, Restraining Orders need to be on the card.
Nice to have
• RELATIONSHIPS. RESPECT. RESULTS. on the back of the card.
Should not have
• Not be too busy/wordy or too flashy.

```html
<!DOCTYPE html>
<html lang="en">
<head>
<meta charset="utf-8">
<title>Vernac Law – Business Card</title>
<link rel="stylesheet" href="https://fonts.googleapis.com/css2?family=Cinzel:wght@400;700&family=Libre+Baskerville&family=Open+Sans:wght@400;600&display=swap">
<style>
  :root {
    --teal: #17abb9;
    --teal-deep: #0d8794;
    --teal-light: #22bdc9;
    --white: #ffffff;
    --paper: #f4f4f4;
    --grey: #b9b9b9;
    --grey-dark: #5c5c5c;
    --backdrop: #e9e6e1;
  }
  * { margin: 0; padding: 0; box-sizing: border-box; }
  html, body {
    width: 1200px; height: 780px; overflow: hidden;
    background: var(--backdrop);
  }
  .canvas { position: relative; width: 1200px; height: 780px; }

  .card {
    position: absolute; top: 100px;
    width: 360px; height: 580px;
    border-radius: 22px; overflow: hidden;
    box-shadow: 0 6px 18px rgba(0,0,0,.18);
  }

  /* Front */
  .card-front { left: 190px; background: linear-gradient(180deg, var(--white), var(--paper)); }
  .card-front .bands { position: absolute; inset: 0; }
  .brand {
    position: absolute; top: 78px; left: 0; width: 100%;
    text-align: center;
  }
  .brand-mark {
    display: inline-block; width: 16px; height: 16px; border-radius: 50%;
    background: var(--teal); vertical-align: middle; margin-right: 10px;
  }
  .brand-name {
    font-family: "Cinzel", serif; font-weight: 400; font-size: 34px;
    color: var(--teal); letter-spacing: 2px; vertical-align: middle;
  }
  .brand-rule {
    width: 180px; height: 1px; background: var(--teal); margin: 14px auto 0;
  }
  .person { position: absolute; top: 150px; left: 0; width: 100%; text-align: center; }
  .person-name {
    font-family: "Cinzel", serif; font-weight: 700; font-size: 25px;
    color: var(--teal); letter-spacing: 1px;
  }
  .person-title {
    font-family: "Libre Baskerville", serif; font-size: 15px;
    color: var(--grey-dark); margin-top: 2px;
  }
  .contact {
    position: absolute; top: 372px; left: 34px; right: 20px;
    font-family: "Open Sans", sans-serif; font-size: 17px; line-height: 27px;
    color: var(--white);
  }
  .contact-row { display: flex; align-items: center; gap: 8px; }
  .contact-row svg { width: 15px; height: 15px; flex: none; }
  .contact-address { margin-bottom: 2px; }

  /* Back */
  .card-back {
    left: 650px;
    background: radial-gradient(circle at 65% 30%, var(--teal-light), var(--teal) 45%, var(--teal-deep));
  }
  .back-content {
    position: absolute; width: 580px; height: 360px;
    left: -110px; top: 110px;
    transform: rotate(90deg);
    display: flex; flex-direction: column; align-items: center; justify-content: center;
    color: var(--white); text-align: center;
  }
  .back-brand {
    font-family: "Cinzel", serif; font-size: 46px; letter-spacing: 3px;
  }
  .back-brand .brand-mark { background: var(--white); width: 20px; height: 20px; margin-right: 14px; }
  .back-rule { width: 230px; height: 1px; background: rgba(255,255,255,.8); margin: 16px 0 30px; }
  .tagline {
    font-family: "Cinzel", serif; font-size: 19px; letter-spacing: 1.5px;
  }
</style>
</head>
<body>
<main class="canvas">

  <section class="card card-front" aria-label="Business card front">
    <svg class="bands" width="360" height="580" viewBox="0 0 360 580" aria-hidden="true">
      <path d="M0,232 Q170,318 360,292 L360,580 L0,580 Z" fill="var(--grey)"/>
      <path d="M0,248 Q170,334 360,308 L360,580 L0,580 Z" fill="var(--teal)"/>
    </svg>

    <div class="brand">
      <span class="brand-mark"></span><span class="brand-name">VERNAC LAW</span>
      <div class="brand-rule"></div>
    </div>

    <div class="person">
      <p class="person-name">ADRIAN MERCER</p>
      <p class="person-title">Managing Director</p>
    </div>

    <div class="contact">
      <p class="contact-address">Southern California,<br>480 Harbor View Blvd. #210</p>
      <p class="contact-row">
        <svg viewBox="0 0 16 16" aria-hidden="true"><path d="M4 1 L6 4 L4.6 5.6 Q6 9 10.4 11.4 L12 10 L15 12 L13.5 15 Q6 14 1 3 Z" fill="var(--white)"/></svg>
        (555) 014-2290
      </p>
      <p class="contact-row">
        <svg viewBox="0 0 16 16" aria-hidden="true"><rect x="1" y="3" width="14" height="10" fill="none" stroke="var(--white)" stroke-width="1.5"/><path d="M1 3 L8 9 L15 3" fill="none" stroke="var(--white)" stroke-width="1.5"/></svg>
        info@vernac-law.example
      </p>
      <p class="contact-row">
        <svg viewBox="0 0 16 16" aria-hidden="true"><circle cx="8" cy="8" r="6.5" fill="none" stroke="var(--white)" stroke-width="1.3"/><ellipse cx="8" cy="8" rx="3" ry="6.5" fill="none" stroke="var(--white)" stroke-width="1.1"/><path d="M1.5 8 H14.5" stroke="var(--white)" stroke-width="1.1"/></svg>
        www.vernac-law.example
      </p>
    </div>
  </section>

  <section class="card card-back" aria-label="Business card back">
    <div class="back-content">
      <p class="back-brand"><span class="brand-mark"></span>VERNAC LAW</p>
      <div class="back-rule"></div>
      <p class="tagline">INTEGRITY. COUNSEL. RESOLVE</p>
    </div>
  </section>

</main>
</body>
</html>
```